Maple n Brook - Contact/Landing Page

I need a landing page which will essentially be the page that customers will go to from the 'website' link on QTV listing. It will provide a short overview of services which need to be selectable. a little further down can capture some contact details followed by a large Submit Now button etc...

I have some icon/logo's that can be utilised at the bottom of the page as industry type references.

Target Market(s)

End of Lease Cleaning Services

Industry/Entity Type

Cleaning Service

Colors

Designer to choose colors to be used in the design.

Requirements
Must have
• As per description
Should not have
• Colours to match my website maplenbrook.com.au

```html
<!DOCTYPE html>
<html lang="en">
<head>
<meta charset="utf-8">
<title>Maple n Brook – End of Lease Cleaning</title>
<link href="https://fonts.googleapis.com/css2?family=Lora:wght@400;600;700&family=Open+Sans:wght@400;600&display=swap" rel="stylesheet">
<style>
:root{
  --brand:#3876bb;
  --ink:#111111;
  --muted:#6b6b6b;
  --line:#d6d6d6;
  --paper:#ffffff;
  --footer:#141414;
  --badge-a:#b9c6dc;
  --badge-b:#2a2a2a;
  --badge-c:#c4cde0;
  --badge-d:#8db84a;
}
*{box-sizing:border-box;margin:0;padding:0}
html,body{width:725px;height:1200px;overflow:hidden;background:var(--paper)}
body{position:relative;font-family:"Lora",serif;color:var(--muted)}
.hero{position:absolute;left:0;top:0;width:725px;height:441px;background:var(--brand)}
.top-icons{position:absolute;top:14px;right:52px;display:flex;gap:14px}
.top-icons svg{width:15px;height:15px}
.brand{position:absolute;top:128px;left:0;width:725px;display:flex;justify-content:center;align-items:center;gap:10px;color:var(--paper);font-size:34px;font-weight:700}
.brand-dot{width:26px;height:26px;border-radius:50%;background:var(--paper)}
.headline{position:absolute;top:278px;left:0;width:725px;text-align:center;color:var(--paper);font-size:26.5px;font-weight:700;letter-spacing:.2px}
.services{position:absolute;top:334px;left:54px;display:flex;gap:7px}
.service{position:relative;width:201px;height:210px;background:var(--paper);border-radius:3px;box-shadow:0 2px 6px rgba(0,0,0,.12);text-align:center;padding-top:33px}
.service-icon{width:38px;height:38px;display:block;margin:0 auto}
.service h2{color:var(--brand);font-size:14.5px;font-weight:600;margin-top:10px;line-height:18px}
.service p{font-size:10.5px;line-height:14.6px;margin:11px auto 0;width:180px}
.select{position:absolute;left:0;right:0;top:152px;font-size:11.5px;line-height:14px;display:flex;justify-content:center;align-items:center;gap:6px}
.box{width:9px;height:9px;border:1.3px solid var(--muted);border-radius:2px}
.tick{width:11px;height:11px;display:block}
.contact-title{position:absolute;top:602px;left:0;width:725px;text-align:center;color:var(--ink);font-size:28px;font-weight:700}
.mail-icon{position:absolute;top:648px;left:357px;width:11px;height:9px}
.email{position:absolute;top:661px;left:0;width:725px;text-align:center;font-size:10.5px}
.form{position:absolute;top:692px;left:107px;width:511px;display:grid;grid-template-columns:1fr 1fr;gap:8px 7px}
.field{height:26px;border:1px solid var(--line);font-size:10px;padding:6px 10px;color:#777}
.field.message{grid-column:1/3;height:65px}
.submit{position:absolute;top:833px;left:313px;width:99px;height:32px;border-radius:16px;background:var(--brand);color:var(--paper);font-size:11.5px;font-weight:700;display:flex;align-items:center;justify-content:center}
.divider{position:absolute;top:907px;left:54px;width:617px;border-top:1px solid #e6e6e6}
.partners{position:absolute;top:946px;left:54px;display:flex;gap:5px}
.partner{width:151px;height:63px;border:1px solid var(--line);display:flex;align-items:center;justify-content:center}
.partner span{display:block}
.footer{position:absolute;left:0;top:1051px;width:725px;height:149px;background:var(--footer);color:var(--paper)}
.regulator{position:absolute;top:38px;left:0;width:725px;text-align:center;font-size:17px;font-weight:600;letter-spacing:.5px}
.licence{position:absolute;top:92px;left:0;width:725px;text-align:center;font-size:12.5px;letter-spacing:.6px}
.legal{position:absolute;top:127px;left:0;width:725px;text-align:center;font-family:"Open Sans",sans-serif;font-size:7.8px}
.code{position:absolute;top:128px;right:19px;font-family:"Open Sans",sans-serif;font-size:7.5px}
</style>
</head>
<body>
<header class="hero">
  <div class="top-icons">
    <svg viewBox="0 0 16 16" fill="none" stroke="#fff" stroke-width="2.2"><circle cx="6.5" cy="6.5" r="4.8"/><path d="M10 10l4.5 4.5" stroke-linecap="round"/></svg>
    <svg viewBox="0 0 16 16" stroke="#fff" stroke-width="2"><path d="M2 3.5h12M2 8h12M2 12.5h12"/></svg>
  </div>
  <div class="brand"><span class="brand-dot"></span>Maple n Brook</div>
  <h1 class="headline">End of Lease Cleaning &nbsp;| &nbsp;Licensed Pest Control</h1>
</header>

<section class="services">
  <article class="service">
    <svg class="service-icon" viewBox="0 0 40 40" fill="none" stroke="#3876bb" stroke-width="1.6"><rect x="5" y="14" width="15" height="20" rx="1"/><path d="M8 14V8h5v6M9 8V4h3"/><rect x="18" y="10" width="7" height="22" rx="1"/><path d="M19 10l2-5h4"/><rect x="22" y="28" width="14" height="8" rx="4"/></svg>
    <h2>Cleaning</h2>
    <p>All interior Cleaning Carried<br>Out to Property Management<br>Requirements</p>
    <div class="select">Select <svg class="tick" viewBox="0 0 12 12" fill="none" stroke="#3876bb" stroke-width="1.6"><rect x="1" y="2" width="9" height="9" rx="1.5"/><path d="M3.5 6.5l2 2L11 2"/></svg></div>
  </article>
  <article class="service">
    <svg class="service-icon" viewBox="0 0 40 40" fill="none" stroke="#3876bb" stroke-width="1.6"><rect x="5" y="3" width="8" height="30" rx="2"/><path d="M13 5h16v17M9 33h10"/><circle cx="27" cy="30" r="6"/><path d="M27 27l-2 4h4z"/><circle cx="20" cy="15" r="3"/><circle cx="24" cy="12" r="2"/></svg>
    <h2>Carpet Cleaning</h2>
    <p>Carpet Steam Cleaning to Australian<br>Standard As 3733:1995</p>
    <div class="select">Select <span class="box"></span></div>
  </article>
  <article class="service">
    <svg class="service-icon" viewBox="0 0 40 40" fill="none" stroke="#3876bb" stroke-width="2"><circle cx="20" cy="20" r="17"/><ellipse cx="20" cy="21" rx="6" ry="9"/><path d="M14 17l-6-3M14 24l-6 3M26 17l6-3M26 24l6 3M8 8l24 24"/></svg>
    <h2>Pest Control</h2>
    <p>Mandatory Requirement For Pets on<br>premises</p>
    <div class="select">Select <span class="box"></span></div>
  </article>
</section>

<h2 class="contact-title">Contact Us</h2>
<svg class="mail-icon" viewBox="0 0 12 9"><rect width="12" height="9" rx="1" fill="#3876bb"/><path d="M0.5 1l5.5 4 5.5-4" stroke="#fff" fill="none" stroke-width="1"/></svg>
<div class="email">info@maplenbrook.com.au</div>

<form class="form">
  <div class="field">First Name</div>
  <div class="field">Sur Name</div>
  <div class="field">Email</div>
  <div class="field">Phone Number</div>
  <div class="field message">Message</div>
</form>
<div class="submit">Submit</div>

<div class="divider"></div>

<section class="partners">
  <div class="partner"><span role="img" aria-label="Partner badge" style="width:128px;height:34px;background:linear-gradient(90deg,var(--badge-a),#d8dfec)"></span></div>
  <div class="partner"><span role="img" aria-label="Certification badge" style="width:114px;height:48px;border-radius:4px;background:var(--badge-b)"></span></div>
  <div class="partner"><span role="img" aria-label="Training partner badge" style="width:76px;height:46px;background:var(--badge-c)"></span></div>
  <div class="partner"><span role="img" aria-label="Accreditation badge" style="width:140px;height:42px;background:var(--badge-d)"></span></div>
</section>

<footer class="footer">
  <div class="regulator">Harbourline Env Authority</div>
  <div class="licence">Pest Licence:4081736</div>
  <div class="legal">© 2021 The Company name. All rights Reserved.Privacy Policy &nbsp;| &nbsp;Terms Of Use</div>
  <div class="code">C28</div>
</footer>
</body>
</html>
```